Soy Candle Labels

We sell soy candles in recycled wine bottles. The wine bottle is cut in half and filled with pure and natural soy wax and scented with essential oils.
Our product represents good use of up cycling materials for a better use. The product is all natural and eco friendly.
You can see good use of labels and branding for a company in America that does the same thing http://larkmeadow7wicks.example/
Trya dn keep the label uncomplicated like the above labels.
We will need an area to hand stamp the scent. Similar to the labels used on the above website.
We would prefer to use a white or off white paper label with gold or bronze printing - limit the use of colour and keep the label simple and sophisticated.
Emberlace Candle Co. is our company name. Emberlace being the predominant name and candle co. written small underneath right justified.
Die cut labels might look better than a rectangle.
Dimensions should be 90mm Wide x 90mm High
The final design should communicate a professional and quality product. But stay modern and professional. Clean, elegant and sophisticated.
Can use wording such as: Hand Poured, Premium Soy Wax, All Natural, Up cycled
Have a look at the attached image for the look and feel we are going for.
Updates
Designers are having a little bit of trouble interpreting the brief into a viable design. To assist perhaps you can look at WINE LABELS on google images. Design your label around an existing style wine label to give the canld ethe feel of being a bottle of wine. Get creative! :)
Reason: We require more designs. We havnt quite got what were looking for.
Please see brief.

```html
<!DOCTYPE html>
<html lang="en">
<head>
<meta charset="utf-8">
<title>Emberlace Candle Co. – Soy Candle Label</title>
<link href="https://fonts.googleapis.com/css2?family=Saira:wght@400;500&family=Saira+Condensed:wght@400;500&display=swap" rel="stylesheet">
<style>
  :root {
    --backdrop: #3a1e10;
    --paper: #fdfcf6;
    --ink: #3b1f12;
    --ink-soft: #6b4a36;
  }
  * { margin: 0; padding: 0; box-sizing: border-box; }
  html, body { width: 1200px; height: 1000px; overflow: hidden; }
  body { background: var(--backdrop); position: relative; font-family: "Saira", sans-serif; color: var(--ink); }

  .label {
    position: absolute; left: 151px; top: 70px; width: 875px; height: 874px;
    background: var(--paper); border-radius: 22px;
  }
  .label__frame {
    position: absolute; left: 15px; top: 16px; right: 16px; bottom: 15px;
    border: 1.5px solid var(--ink); border-radius: 14px;
  }

  .claims { position: absolute; left: 43px; top: 36px; line-height: 1; }
  .claims__title { font-size: 37px; font-weight: 500; margin-bottom: 12px; }
  .claims__line { font-size: 26px; font-weight: 400; margin-bottom: 9px; }

  .scent-stamp { position: absolute; left: 597px; top: 36px; width: 216px; height: 216px; }

  .brand { position: absolute; right: 52px; top: 365px; text-align: right; line-height: 1; }
  .brand__name { font-size: 132px; font-weight: 400; letter-spacing: 1px; }
  .brand__sub { font-size: 30px; font-weight: 400; margin-top: 14px; margin-right: 24px; }

  .ornament-band {
    position: absolute; left: 16px; top: 630px; width: 843px; height: 82px;
    background: linear-gradient(180deg, #d9ccc2 0%, #8a6a58 50%, #d9ccc2 100%);
  }

  .footer-note {
    position: absolute; top: 768px; font-family: "Saira Condensed", sans-serif;
    font-size: 44px; font-weight: 500; line-height: 1; display: flex; align-items: center;
  }
  .footer-note--origin { left: 45px; }
  .footer-note--material { right: 42px; }
  .footer-note__rule { width: 2px; height: 50px; background: var(--ink); margin: 0 6px 0 16px; }
  .footer-note--material .footer-note__rule { margin: 0 14px 0 6px; }
  .footer-note__flourish { width: 50px; height: 26px; background: var(--ink-soft); opacity: .55; border-radius: 13px; }
</style>
</head>
<body>
  <main class="label">
    <div class="label__frame"></div>

    <section class="claims">
      <p class="claims__title">Hand Poured</p>
      <p class="claims__line">All Natural Soy</p>
      <p class="claims__line">320 gm of Premium Soy Wax</p>
    </section>

    <svg class="scent-stamp" viewBox="0 0 216 216" aria-label="Area for hand-stamped scent">
      <circle cx="108" cy="108" r="106" fill="none" stroke="#3b1f12" stroke-width="1"/>
    </svg>

    <section class="brand">
      <p class="brand__name">Emberlace</p>
      <p class="brand__sub">Candle Co.</p>
    </section>

    <div class="ornament-band" role="img" aria-label="Decorative scroll ornament band across the label"></div>

    <p class="footer-note footer-note--origin">
      Product of Australia
      <span class="footer-note__rule"></span>
      <span class="footer-note__flourish" role="img" aria-label="Small scroll flourish"></span>
    </p>
    <p class="footer-note footer-note--material">
      <span class="footer-note__flourish" role="img" aria-label="Small scroll flourish"></span>
      <span class="footer-note__rule"></span>
      up-cycled wine bottle
    </p>
  </main>
</body>
</html>
```